Design Sales-Funnel page for our beauty brand*

Hi all,

we are a beauty brand located in Romania (Eastern-Europe) and we are using sales-funnel pages to sell our own make-up brushes.

We have a ready design (see download-link) that we are not totally happy with, so we want you to create a new version of it, which fits more to our companies website

www.lumavela.rowhich

is very clean and easy to read for our customers.

So, your task is to

1) re-create the main page of our sales funnel
2) according to your design from 1) create the upsell/downsell and thank-you page as well.

What we do not like about the actual design:
- it is not clean/simple enough = hard for the customer eye to catch the content. What do we mean with that? There are too many background frames, too many different colors used.
- The original price for our brushes is 1.299 LEI and for this sale, we are giving it away for 399 LEI (LEI = Romanian currency). The discount is 70%, but it does not show on the page enough.

You can download all files here:
https://www.filecrate-share.com/sh/4kqtpx2mw915bd/QXZrTnHvLpEeKcYwMbDoUfsJa?dl=0

Thanks,
Mirela

Target Market(s)

Women 18-35

Industry/Entity Type

Makeup

Number of Pages Required

4 page

Font styles to use
Sans Serif

Colors

Designer to choose colors to be used in the design.

Requirements
Must have
• See description
Nice to have
• See description
Should not have
• See description

```html
<!DOCTYPE html>
<html lang="en">
<head>
<meta charset="UTF-8">
<title>Before You Go – Brush Set Offer</title>
<link rel="stylesheet" href="https://fonts.googleapis.com/css2?family=Open+Sans:wght@400;700&family=Playfair+Display:wght@700;800&display=swap">
<style>
  :root {
    --page-bg: #ecf1f3;
    --card-bg: #ffffff;
    --brand-red: #c42535;
    --ink: #444444;
    --photo-light: #ffffff;
    --photo-shade: #e9e6e4;
  }
  * { margin: 0; padding: 0; box-sizing: border-box; }
  html, body { width: 1200px; height: 1061px; overflow: hidden; }
  body {
    position: relative;
    background: var(--page-bg);
    font-family: "Open Sans", Arial, sans-serif;
    color: var(--ink);
  }
  .headline {
    position: absolute; left: 0; top: 52px; width: 1200px;
    text-align: center;
    font-family: "Playfair Display", Georgia, serif;
    font-weight: 800; font-size: 60px; letter-spacing: -1.5px;
    color: var(--brand-red); line-height: 1;
  }
  .subhead {
    position: absolute; left: 0; top: 148px; width: 1200px;
    text-align: center; font-size: 27px; line-height: 33px;
  }
  .subhead .lead { letter-spacing: 3px; }
  .subhead strong { font-weight: 700; display: block; }
  .offer-card {
    position: absolute; left: 82px; top: 325px;
    width: 1036px; height: 468px;
    background: var(--card-bg); border-radius: 33px; overflow: hidden;
  }
  .product-photo {
    position: absolute; left: 0; top: 0; width: 450px; height: 468px;
    background: linear-gradient(90deg, var(--photo-light) 0%, var(--photo-shade) 55%, var(--photo-light) 100%);
    opacity: .6;
  }
  .price-tag {
    position: absolute; left: 460px; top: 244px; width: 280px; height: 110px;
    background: var(--card-bg); border-radius: 26px;
    box-shadow: 0 6px 18px rgba(0,0,0,.12);
    display: flex; align-items: center; justify-content: center;
    font-family: "Playfair Display", Georgia, serif; font-weight: 700;
    font-size: 34px; color: var(--ink); z-index: 2;
  }
  .price-tag .amount { color: var(--brand-red); margin: 0 9px; }
  .offer-copy {
    position: absolute; left: 569px; top: 398px; width: 480px;
    font-size: 21px; line-height: 33px; letter-spacing: .3px;
  }
  .offer-copy .highlight { color: var(--brand-red); font-weight: 700; }
  .set-title {
    position: absolute; left: 569px; top: 530px;
    font-size: 21px; font-weight: 700; letter-spacing: .4px;
  }
  .set-items { position: absolute; left: 569px; top: 596px; list-style: none; }
  .set-items li {
    position: relative; padding-left: 33px;
    font-size: 22px; line-height: 45px; letter-spacing: .3px;
  }
  .set-items li::before {
    content: ""; position: absolute; left: 0; top: 15px;
    width: 14px; height: 14px; border-radius: 50%; background: var(--brand-red);
  }
  .add-button {
    position: absolute; left: 601px; top: 758px; width: 413px; height: 110px;
    background: var(--brand-red); border-radius: 27px;
    box-shadow: 0 6px 14px rgba(0,0,0,.12);
    display: flex; align-items: center; justify-content: center;
    font-family: "Playfair Display", Georgia, serif; font-weight: 700;
    font-size: 35px; color: #fff; letter-spacing: -.3px; z-index: 2;
  }
  .decline-link {
    position: absolute; left: 601px; top: 895px; width: 413px;
    text-align: center;
    font-family: "Playfair Display", Georgia, serif; font-weight: 700;
    font-size: 30px; color: var(--ink); letter-spacing: .5px;
  }
</style>
</head>
<body>
  <h1 class="headline">BEFORE YOU GO</h1>
  <p class="subhead"><span class="lead">add to your order the</span><strong>essentials 3x brushes set</strong></p>

  <div class="price-tag">ONLY<span class="amount">99</span>LEI</div>

  <section class="offer-card">
    <div class="product-photo" role="img" aria-label="Three red-handled makeup brushes with cream bristles laid on a white surface"></div>
  </section>

  <p class="offer-copy">Before we complete your order, I’d like to make you a special one time offer that you will <span class="highlight">only see on this page</span></p>
  <h2 class="set-title">MOST LOVED 3X BRUSHES SET:</h2>
  <ul class="set-items">
    <li>1x foundation brush</li>
    <li>1x powder/blush brush</li>
    <li>1x blending brush</li>
  </ul>

  <div class="add-button">ADD TO MY ORDER</div>
  <div class="decline-link">NO THANKS, I’LL PASS</div>
</body>
</html>
```